new letterhead for my brokergae company KeelBright, Complete Marine Brokering

We need a new letterhead for our brokerage company called KeelBright. We are specialised in selling pleasure crafts (sailing and motoryachts). More info can be found at https://keelbright-example.com/en

I use this document for a quotation, a letter, sales agreement, selling instructions. I am looking for a cover page + a content page.

Th efollowing information needs to be in the header / footer; email, website, VAT number, Bank Account number, number chamber of ccomerce, registry number olpa, General terms and conditions TQRV apply.

```html
<!DOCTYPE html>
<html lang="en">
<head>
<meta charset="utf-8">
<title>KeelBright Letterhead</title>
<link href="https://fonts.googleapis.com/css2?family=Open+Sans:wght@400;600;700&display=swap" rel="stylesheet">
<style>
  :root {
    --backdrop: #cfdafb;
    --paper: #f6f6f5;
    --brand-blue: #1a5aa8;
    --ink: #4a4a4a;
    --rule: #9a9a9a;
  }
  * { margin: 0; padding: 0; box-sizing: border-box; }
  html, body {
    width: 1200px; height: 900px; overflow: hidden;
    background: var(--backdrop);
    font-family: "Open Sans", Arial, sans-serif;
  }
  .letterhead {
    position: absolute;
    left: 303px; top: 30px;
    width: 594px; height: 840px;
    background: var(--paper);
    box-shadow: 0 2px 10px rgba(40, 60, 120, 0.15);
  }
  .brand {
    position: absolute; left: 42px; top: 40px;
    color: var(--brand-blue);
  }
  .brand-name {
    font-size: 28px; font-weight: 600; line-height: 1;
    letter-spacing: -0.2px;
  }
  .brand-tagline {
    margin-top: 6px;
    font-size: 7.5px; font-weight: 600; letter-spacing: 1.6px;
    text-transform: uppercase;
  }
  .contact {
    position: absolute; left: 455px; top: 66px;
    padding-left: 8px;
    border-left: 3px solid var(--brand-blue);
    font-size: 8.5px; line-height: 11px; color: var(--ink);
  }
  .contact-item { display: flex; align-items: center; gap: 5px; }
  .contact-item svg { width: 7px; height: 7px; fill: none; stroke: var(--brand-blue); stroke-width: 1.6; }
  .footer {
    position: absolute; left: 14px; right: 14px; top: 768px;
    text-align: center; color: var(--ink);
  }
  .registration {
    font-size: 7.4px; padding-bottom: 4px;
    border-bottom: 1px solid var(--rule);
  }
  .terms {
    margin-top: 4px;
    font-size: 7.2px; line-height: 10px;
  }
  .base-band {
    position: absolute; left: 0; right: 0; bottom: 0; height: 8px;
    background: var(--brand-blue);
  }
</style>
</head>
<body>
  <main class="letterhead">
    <header>
      <div class="brand">
        <div class="brand-name">KeelBright</div>
        <div class="brand-tagline">Complete Marine Brokering</div>
      </div>
      <address class="contact" style="font-style:normal">
        <div class="contact-item">
          <svg viewBox="0 0 10 10"><path d="M2 1 L4 1 L4.5 3.5 L3.2 4.3 Q4.3 6.5 5.7 6.8 L6.5 5.5 L9 6 L9 8 Q5 9.5 1 2 Z"/></svg>
          <span>+31 20 555 01 48</span>
        </div>
        <div class="contact-item">
          <svg viewBox="0 0 10 10"><rect x="1" y="2.5" width="8" height="5.5"/><path d="M1 2.5 L5 5.5 L9 2.5"/></svg>
          <span>info@keelbright-example.com</span>
        </div>
        <div class="contact-item">
          <svg viewBox="0 0 10 10"><circle cx="5" cy="5" r="4"/><path d="M1 5 H9 M5 1 Q2.5 5 5 9 M5 1 Q7.5 5 5 9"/></svg>
          <span>www.keelbright-example.com</span>
        </div>
      </address>
    </header>

    <footer class="footer">
      <p class="registration">VAT # 0000000 | Bank Account #: 0000 0000 0000 0000 | # Chamber of Commerce | Registry Number OLPA</p>
      <p class="terms">These general terms and conditions have been laid down by the 'Harbour Guild of Vessel Agents' (Nederlandse Gilde van Scheepsagenten, TQRV) and filed at the court registry of the court in Amsterdam on 13/04/2017 under number 28/2017 in Dutch. These terms and conditions apply exclusively to members of the TQRV. The terms and conditions came into force on 15/03/2017. ©Harbour Guild of Vessel Agents.</p>
    </footer>
    <div class="base-band"></div>
  </main>
</body>
</html>
```